Alaska Law Firm Needs a Sticker Design

We need a design for stickers to put on already-printed brochures. We mail the brochures to potential clients so they can learn more about accident-induced injuries, insurance claims, legal representation, and our own law firm.

One of our lawyers wrote a book that provides a helpful overview of personal injury claims. We are offering this book for free to anyone who calls and requests it. Therefore, the sticker design should include one of the following phrases, or something very similar:
a) "Still have questions? Call and request our book-- for free!"
b) "Still have questions about auto accident claims? Call and request our book today."
c) "Still have questions about filing a claim? Call and request a free copy of our book."
d) "Still have questions? Call us today to request a free copy of our book, Clear Lanes Ahead."
e) "To learn more about automobile accidents and insurance, call today and request a free copy of our book."

The sticker should be approximately 3"x3" and may be a circle, square, rectangle, or ellipsis. The sticker will be placed on the back of the folder, which is light blue. We would like the sticker to match the color scheme of our website and the folder.

I will upload an image of the book cover as soon as I obtain it.

Law Firm

Font styles to use
Serif
Sans Serif

Requirements
Should not have
• Bright colors that aren't already used in the folder design. e.g. no bright orange, pink, chartreuse, turquoise, yellow, red.

```html
<!DOCTYPE html>
<html lang="en">
<head>
<meta charset="utf-8">
<title>Free Book Sticker</title>
<link href="https://fonts.googleapis.com/css2?family=Cinzel:wght@400;500&family=Roboto+Condensed:wght@300;400;800&family=Open+Sans:wght@400;600&family=Arimo&display=swap" rel="stylesheet">
<style>
:root{
  --navy:#153f69;
  --sky:#d9e6f7;
  --ink:#13153f;
  --pale:#e2ecf9;
  --paper:#ffffff;
  --alert:#c0282d;
  --body:#2b2b2b;
}
html,body{margin:0;padding:0;width:1200px;height:1200px;overflow:hidden;background:var(--paper);}
.sticker{position:relative;width:1200px;height:1200px;}
.sticker-shape{position:absolute;inset:0;}
.headline{position:absolute;left:0;width:1200px;text-align:center;color:var(--paper);font-family:"Cinzel",serif;line-height:1;white-space:nowrap;}
.headline-lead{top:160px;font-size:92px;}
.headline-main{top:258px;font-size:128px;}
.headline-offer{top:401px;font-size:66px;}
.headline-free{top:486px;font-size:96px;}
.phone{position:absolute;left:0;top:1070px;width:1200px;text-align:center;font-family:"Arimo",sans-serif;font-size:54px;line-height:1;color:var(--pale);}

.book{position:absolute;left:358px;top:641px;width:463px;height:355px;border:2px solid var(--ink);background:var(--paper);overflow:hidden;}
.book-back{position:absolute;left:0;top:0;width:230px;height:317px;}
.book-spine{position:absolute;left:230px;top:0;width:9px;height:359px;background:var(--ink);}
.spine-text{position:absolute;left:1px;top:110px;writing-mode:vertical-rl;font-family:"Roboto Condensed",sans-serif;font-size:5px;color:var(--paper);white-space:nowrap;letter-spacing:.3px;}
.spine-text span{margin-top:14px;display:inline-block;font-weight:300;}
.book-front{position:absolute;left:239px;top:0;width:228px;height:317px;}
.book-base{position:absolute;left:0;top:317px;width:467px;height:42px;background:var(--ink);}
.base-notch{position:absolute;left:140px;top:317px;width:80px;height:23px;background:var(--paper);}

.blurb{position:absolute;font-family:"Open Sans",sans-serif;font-size:5px;line-height:1.3;color:var(--body);margin:0;text-align:justify;}
.blurb-alert{left:18px;top:14px;width:194px;color:var(--alert);font-weight:600;text-align:center;text-transform:uppercase;}
.blurb-one{left:22px;top:40px;width:190px;}
.blurb-two{left:22px;top:62px;width:190px;}
.back-rule{position:absolute;left:44px;top:102px;width:150px;height:1px;background:var(--alert);}
.headshot{position:absolute;left:21px;top:113px;width:56px;height:75px;background:linear-gradient(160deg,#d8d9dc 0%,#9aa7b8 40%,#2a5aa8 100%);}
.bio-side{left:83px;top:113px;width:129px;}
.bio-side + .bio-side{top:146px;}
.bio-wide{left:21px;width:191px;}
.bio-three{top:196px;}
.bio-four{top:224px;}
.bio-five{top:251px;}
.firm-mark{position:absolute;left:22px;top:286px;display:flex;align-items:center;gap:5px;font-family:"Open Sans",sans-serif;font-size:8px;color:var(--ink);letter-spacing:.4px;text-transform:uppercase;}
.firm-mark i{display:block;width:14px;height:14px;background:var(--ink);}

.author{position:absolute;left:0;top:16px;width:228px;text-align:center;font-family:"Roboto Condensed",sans-serif;font-weight:300;font-size:15px;color:var(--ink);letter-spacing:-.2px;}
.title{position:absolute;left:0;top:38px;width:228px;text-align:center;font-family:"Roboto Condensed",sans-serif;font-weight:800;font-size:28px;line-height:.98;color:var(--ink);letter-spacing:-.5px;}
.cover-photo{position:absolute;left:0;top:100px;width:228px;height:217px;background:linear-gradient(180deg,#eef1f3 0%,#c9d7c4 35%,#8fae5a 70%,#6f9a3c 100%);}
.subtitle{position:absolute;left:239px;top:326px;width:228px;text-align:center;font-family:"Roboto Condensed",sans-serif;font-size:11px;line-height:1.25;color:var(--paper);}
</style>
</head>
<body>
<div class="sticker">
  <svg class="sticker-shape" width="1200" height="1200" viewBox="0 0 1200 1200" aria-hidden="true">
    <defs>
      <clipPath id="sticker-outline"><ellipse cx="600" cy="624" rx="600" ry="557"/></clipPath>
    </defs>
    <g clip-path="url(#sticker-outline)">
      <rect x="0" y="0" width="1200" height="1200" fill="var(--navy)"/>
      <rect x="0" y="604" width="1200" height="442" fill="var(--sky)"/>
    </g>
  </svg>

  <div class="headline headline-lead">Still have</div>
  <div class="headline headline-main">QUESTIONS?</div>
  <div class="headline headline-offer">Call and request our book</div>
  <div class="headline headline-free">FOR FREE</div>

  <div class="book">
    <div class="book-back">
      <p class="blurb blurb-alert">Most of us will be involved in a car accident at least once. Many will face three or four.</p>
      <p class="blurb blurb-one">If you have never had a crash, be glad. It still pays to know what to do before it happens.</p>
      <p class="blurb blurb-two">If you were recently hurt on the road, the pages ahead explain your rights and the steps to take next.</p>
      <div class="back-rule"></div>
      <div class="headshot" role="img" aria-label="Author portrait photo"></div>
      <p class="blurb bio-side">A science graduate, Daniel chose law school over medicine after college.</p>
      <p class="blurb bio-side">He began his career defending doctors and insurers, then learned his place was beside the injured person.</p>
      <p class="blurb bio-wide bio-three">He opened a firm for injured people and has since helped thousands receive fair pay.</p>
      <p class="blurb bio-wide bio-four">In 2010 he moved to Alaska and founded Hartwell Law Group, serving hundreds of local families.</p>
      <p class="blurb bio-wide bio-five">Most cases settle out of court, yet insurers pay fairly when the threat of a trial is real.</p>
      <div class="firm-mark"><i></i>Hartwell Law Group</div>
    </div>
    <div class="book-base"></div>
    <div class="base-notch"></div>
    <div class="book-spine"><div class="spine-text">CLEAR LANES AHEAD <span>DANIEL R. HARTWELL</span></div></div>
    <div class="book-front">
      <div class="author">DANIEL R. HARTWELL</div>
      <div class="title">CLEAR LANES<br>AHEAD</div>
      <div class="cover-photo" role="img" aria-label="Cover photo of a smiling family lying on grass in a park beside a small red toy car"></div>
    </div>
    <div class="subtitle">THE RIGHT WAY TO HANDLE<br>YOUR AUTO ACCIDENT CLAIM</div>
  </div>

  <div class="phone">(907) 555- 0142</div>
</div>
</body>
</html>
```